Calloway needs a modernized design

We would like a modern update (that can be responsive) to our existing website. Attached are the two existing pages we would like new concepts of - our home page and a page about one of our locations.

Calloway is provides executive offices and virtual office services. Startups, law firms, and financial services are our primary clients. We would like a professional, clean design, leaning towards minimalist. We intend to greatly reduce/eliminate the long paragraphs of text.

Requirements
Must have
• A design that can be responsive
Nice to have
• Large image(s) on home page that rotate.

```html
<!DOCTYPE html>
<html lang="en">
<head>
<meta charset="utf-8">
<title>Calloway Business Centers</title>
<link href="https://fonts.googleapis.com/css2?family=Raleway:wght@400;500;600&family=Open+Sans:wght@400;600&display=swap" rel="stylesheet">
<style>
:root{
  --navy:#25336a;
  --orange:#ffa400;
  --sky:#1ea2e0;
  --gray-band:#f2f2f2;
  --ink:#333;
  --muted:#777;
  --white:#fff;
  --black:#000;
}
*{box-sizing:border-box;margin:0;padding:0}
html,body{width:1200px;height:2436px;overflow:hidden}
body{position:relative;background:var(--white);font-family:"Open Sans",Arial,sans-serif;color:var(--ink)}
.abs{position:absolute}
h1,h2,h3{font-weight:400}

/* header */
.site-header{left:0;top:0;width:1200px;height:100px;background:var(--white)}
.brand{left:184px;top:22px;display:flex;align-items:center;gap:10px}
.brand-dot{width:56px;height:56px;border-radius:50%;background:var(--navy)}
.brand-name{font-family:"Raleway",sans-serif;font-weight:600;font-size:16px;line-height:19px;color:var(--navy);letter-spacing:.5px;width:120px}
.main-nav{left:424px;top:45px;display:flex;gap:22px;font-family:"Raleway",sans-serif;font-size:14px;font-weight:500;color:#333}
.main-nav .active{color:var(--navy)}

/* hero */
.hero{left:0;top:100px;width:1200px;height:512px;
  background:
    radial-gradient(ellipse 160px 260px at 370px 400px,rgba(220,225,235,.85),transparent 70%),
    radial-gradient(ellipse 260px 120px at 820px 480px,rgba(90,120,170,.45),transparent 70%),
    radial-gradient(ellipse 200px 220px at 1080px 250px,rgba(120,170,175,.55),transparent 70%),
    linear-gradient(90deg,#7d8a98 0%,#aab6c2 18%,#e4e8ee 40%,#eef1f4 62%,#c9d3dc 82%,#8a9aa8 100%)}
.hero-title{left:0;top:266px;width:1200px;text-align:center;font-family:"Raleway",sans-serif;font-size:45px;font-weight:500;color:var(--white);text-shadow:0 1px 6px rgba(0,0,0,.2)}
.hero-sub{left:0;top:326px;width:1200px;text-align:center;font-family:"Raleway",sans-serif;font-size:26px;font-weight:500;color:var(--white);letter-spacing:.5px;text-shadow:0 1px 6px rgba(0,0,0,.2)}
.hero-btn{left:538px;top:375px;width:125px;height:35px;border:2px solid var(--white);color:var(--white);font-family:"Raleway",sans-serif;font-size:12px;font-weight:600;display:flex;align-items:center;justify-content:center}
.hero-dots{left:563px;top:578px;display:flex;gap:5px}
.hero-dots span{width:15px;height:15px;border-radius:50%;background:var(--white)}
.hero-dots span.current{background:transparent;border:2px solid var(--white)}

/* intro */
.intro-title{left:0;top:678px;width:1200px;text-align:center;font-family:"Raleway",sans-serif;font-size:30px;font-weight:500;color:#333}
.intro-text{left:210px;top:732px;width:780px;text-align:center;font-size:11px;line-height:19px;color:var(--muted)}

/* services */
.services{left:0;top:856px;width:1200px;height:341px;background:var(--gray-band);border:2px solid #ddd}
.arrow{top:988px}
.service{top:909px;width:260px;text-align:center}
.service-icon{display:block;margin:0 auto}
.service h3{margin-top:20px;font-family:"Raleway",sans-serif;font-size:16px;font-weight:500;line-height:20px;color:#333}
.service p{margin-top:10px;font-size:11px;line-height:19px;color:#555}
.service .read-more{display:inline-block;margin-top:12px;width:97px;height:27px;line-height:23px;border:2px solid #333;font-family:"Raleway",sans-serif;font-size:10px;font-weight:600;color:#111}

/* feature bands */
.band{left:0;width:1200px;height:391px;display:block}
.band-values{top:1197px}
.band-community{top:1588px;height:395px}
.feature-title{font-family:"Raleway",sans-serif;font-size:32px;font-weight:400;color:var(--white)}
.feature-text{font-size:11px;line-height:20px;color:var(--white)}
.outline-btn{width:122px;height:38px;border:2px solid var(--white);color:var(--white);font-size:13px;display:flex;align-items:center;justify-content:center}

/* request */
.request{left:0;top:1983px;width:1200px;height:299px;
  background:
    radial-gradient(ellipse 180px 200px at 930px 120px,rgba(222,178,150,.8),transparent 70%),
    radial-gradient(ellipse 200px 160px at 180px 120px,rgba(70,50,40,.6),transparent 70%),
    radial-gradient(ellipse 260px 120px at 420px 280px,rgba(150,110,90,.6),transparent 70%),
    linear-gradient(90deg,#5e463a 0%,#9c8270 30%,#7a6152 55%,#b89580 75%,#6d5a52 100%)}
.request-title{left:0;top:2033px;width:1200px;text-align:center;font-family:"Raleway",sans-serif;font-size:30px;font-weight:400;color:var(--white)}
.field{width:242px;height:36px;background:var(--white);font-size:12px;color:#666;padding:0 16px;display:flex;align-items:center}
.submit{left:518px;top:2199px;width:146px;height:41px;background:linear-gradient(#30b4ef,#1590cf);color:var(--white);font-family:"Raleway",sans-serif;font-weight:600;font-size:16px;display:flex;align-items:center;justify-content:center}

/* footer */
.site-footer{left:0;top:2282px;width:1200px;height:154px;background:var(--black)}
.footer-nav{left:0;top:2322px;width:1200px;display:flex;justify-content:center;gap:34px;font-family:"Raleway",sans-serif;font-size:13px;color:var(--white)}
.copyright{left:0;top:2349px;width:1200px;text-align:center;font-size:10px;color:#bbb}
.social{left:530px;top:2376px;display:flex;gap:8px}
.social span{width:32px;height:32px;border-radius:50%;background:var(--white)}
</style>
</head>
<body>

<header class="site-header abs">
  <div class="brand abs"><span class="brand-dot"></span><span class="brand-name">CALLOWAY BUSINESS CENTERS</span></div>
  <nav class="main-nav abs">
    <span class="active">HOME</span><span>PROPERTIES</span><span>VIRTUAL TOURS &amp; VIDEOS</span><span>PHOTOS</span><span>BROKER REFERRALS</span>
  </nav>
</header>

<section class="hero abs" role="img" aria-label="Photo of a businesswoman standing in a bright office while colleagues meet at a conference table"></section>
<h1 class="hero-title abs">FINANCIAL SERVICES &amp; LAW FIRM</h1>
<p class="hero-sub abs">MAECENAS ALIQUET VELIT VEL TURPIS</p>
<div class="hero-btn abs">LEARN MORE</div>
<div class="hero-dots abs"><span class="current"></span><span></span><span></span><span></span></div>

<h2 class="intro-title abs">CALLOWAY BUSINESS CENTERS</h2>
<p class="intro-text abs">Duis sed tellus et tortor vestibulum gravida Praesent elementum elit at tellus Curabitur metus ipsum luctus eu malesuada sit tincidunt sed diam Donec quis mi sed magna hendrerit accumsan Suspendisse risus nibh ultricies eu volutpat non condimentum hendrerit augue Etiam eleifend metus vitae adipiscing semper mauris ipsum iaculis elit congue gravida elit mi egestas orci Curabitur pede</p>

<section class="services abs"></section>
<svg class="arrow abs" style="left:174px" width="20" height="32" viewBox="0 0 20 32"><path d="M16 2 L4 16 L16 30" fill="none" stroke="#aaa" stroke-width="3"/></svg>
<svg class="arrow abs" style="left:1010px" width="20" height="32" viewBox="0 0 20 32"><path d="M4 2 L16 16 L4 30" fill="none" stroke="#aaa" stroke-width="3"/></svg>

<div class="service abs" style="left:198px">
  <svg class="service-icon" width="114" height="114" viewBox="0 0 114 114" aria-hidden="true">
    <circle cx="57" cy="57" r="57" fill="var(--orange)"/>
    <path d="M57 0 A57 57 0 0 1 57 114 Z" fill="#ff9500"/>
    <g fill="#fff">
      <circle cx="38" cy="42" r="7"/><path d="M28 52h20v26h-20z"/>
      <circle cx="57" cy="38" r="8"/><path d="M46 50h22v32h-22z"/>
      <circle cx="76" cy="42" r="7"/><path d="M66 52h20v26h-20z"/>
    </g>
    <g fill="var(--orange)"><path d="M56 50h2l1 14-2 3-2-3z"/></g>
  </svg>
  <h3>EXECUTIVE OFFICE<br>SUITES</h3>
  <p>Maecenas aliquet velit vel turpis Mauris neque<br>metus malesuada nec ultricies sit</p>
  <span class="read-more">READ MORE</span>
</div>
<div class="service abs" style="left:470px">
  <svg class="service-icon" width="114" height="114" viewBox="0 0 114 114" aria-hidden="true">
    <circle cx="57" cy="57" r="57" fill="var(--navy)"/>
    <circle cx="57" cy="57" r="53" fill="none" stroke="#3a4a85" stroke-width="2"/>
    <g fill="none" stroke="#fff" stroke-width="2.5">
      <rect x="45" y="26" width="24" height="16" rx="3"/>
      <path d="M52 42l-3 5 7-5"/>
    </g>
    <g fill="#fff">
      <circle cx="35" cy="52" r="6"/><path d="M28 60h14v18h-14z"/>
      <circle cx="79" cy="52" r="6"/><path d="M72 60h14v18h-14z"/>
      <rect x="40" y="64" width="34" height="5"/>
      <rect x="55" y="69" width="4" height="16"/>
      <rect x="24" y="78" width="4" height="10"/><rect x="86" y="78" width="4" height="10"/>
    </g>
  </svg>
  <h3>ON DEMAND MEETING<br>ROOMS</h3>
  <p>Maecenas aliquet velit vel turpis Mauris neque<br>metus malesuada nec ultricies sit</p>
  <span class="read-more">READ MORE</span>
</div>
<div class="service abs" style="left:749px">
  <svg class="service-icon" width="114" height="114" viewBox="0 0 114 114" aria-hidden="true">
    <circle cx="57" cy="57" r="57" fill="var(--sky)"/>
    <circle cx="57" cy="57" r="53" fill="none" stroke="#4bb8ea" stroke-width="2"/>
    <g fill="#fff">
      <rect x="30" y="42" width="22" height="40"/>
      <rect x="54" y="30" width="30" height="52"/>
      <rect x="26" y="82" width="62" height="4"/>
    </g>
    <g fill="var(--sky)">
      <rect x="34" y="48" width="5" height="5"/><rect x="43" y="48" width="5" height="5"/>
      <rect x="34" y="58" width="5" height="5"/><rect x="43" y="58" width="5" height="5"/>
      <rect x="34" y="68" width="5" height="5"/><rect x="43" y="68" width="5" height="5"/>
      <rect x="59" y="36" width="6" height="6"/><rect x="73" y="36" width="6" height="6"/>
      <rect x="59" y="47" width="6" height="6"/><rect x="73" y="47" width="6" height="6"/>
      <rect x="59" y="58" width="6" height="6"/><rect x="73" y="58" width="6" height="6"/>
      <rect x="65" y="70" width="8" height="12"/>
    </g>
  </svg>
  <h3>VIRTUAL OFFICE<br>SOLUTIONS</h3>
  <p>Maecenas aliquet velit vel turpis Mauris neque<br>metus malesuada nec ultricies sit</p>
  <span class="read-more">READ MORE</span>
</div>

<svg class="band band-values abs" viewBox="0 0 1200 391" width="1200" height="391" preserveAspectRatio="none">
  <defs>
    <linearGradient id="valuesPhoto" x1="0" y1="0" x2="1" y2="1">
      <stop offset="0" stop-color="#c9ced6"/>
      <stop offset=".35" stop-color="#eef0f3"/>
      <stop offset=".6" stop-color="#dfe2e7"/>
      <stop offset=".8" stop-color="#7c8794"/>
      <stop offset="1" stop-color="#4d5662"/>
    </linearGradient>
    <radialGradient id="valuesGlow" cx=".75" cy=".2" r=".35">
      <stop offset="0" stop-color="#3d4550" stop-opacity=".7"/>
      <stop offset="1" stop-color="#3d4550" stop-opacity="0"/>
    </radialGradient>
  </defs>
  <g role="img" aria-label="Photo of business partners reviewing financial reports beside a laptop">
    <rect width="1200" height="391" fill="url(#valuesPhoto)"/>
    <rect width="1200" height="391" fill="url(#valuesGlow)"/>
  </g>
  <path d="M0 0 H700 C625 60 600 150 615 245 C625 320 610 375 555 391 H0 Z" fill="var(--orange)" stroke="#fff" stroke-opacity=".6" stroke-width="4"/>
</svg>
<h2 class="feature-title abs" style="left:180px;top:1292px">Our Values</h2>
<p class="feature-text abs" style="left:182px;top:1336px;width:410px">Either you need Dallas/Ft. Worth Office Space, Dallas Executive Suites, Ft. Worth Executive Suites, Houston Office Space, Houston Executive Suites, or maybe you simply need a place to stop in and use an on-demand office or meeting room from time to time or utilize our local business phone numbers, phone answering or business addresses through one of our virtual office solutions.</p>
<div class="outline-btn abs" style="left:182px;top:1453px">Learn More</div>

<svg class="band band-community abs" viewBox="0 0 1200 395" width="1200" height="395" preserveAspectRatio="none">
  <defs>
    <linearGradient id="communityPhoto" x1="0" y1="0" x2="1" y2="1">
      <stop offset="0" stop-color="#3f3a3a"/>
      <stop offset=".3" stop-color="#c9a57c"/>
      <stop offset=".55" stop-color="#e6e3de"/>
      <stop offset=".8" stop-color="#b99670"/>
      <stop offset="1" stop-color="#6a5c55"/>
    </linearGradient>
    <radialGradient id="communityPaper" cx=".3" cy=".55" r=".25">
      <stop offset="0" stop-color="#f4f4f2" stop-opacity=".8"/>
      <stop offset="1" stop-color="#f4f4f2" stop-opacity="0"/>
    </radialGradient>
  </defs>
  <g role="img" aria-label="Photo from above of colleagues discussing documents around a wooden table">
    <rect width="1200" height="395" fill="url(#communityPhoto)"/>
    <rect width="1200" height="395" fill="url(#communityPaper)"/>
  </g>
  <path d="M615 0 C575 70 585 160 600 230 C615 310 625 370 670 395 H1200 V0 Z" fill="var(--navy)" stroke="#fff" stroke-opacity=".5" stroke-width="4"/>
</svg>
<h2 class="feature-title abs" style="left:638px;top:1688px">Our Community</h2>
<p class="feature-text abs" style="left:642px;top:1740px;width:410px">Companies that partner with Calloway share more than a prestigious address. They also share ideas and services. Our Executive Office Business Centers are places where savvy, growing companies can network, interact and learn from one another.</p>
<div class="outline-btn abs" style="left:643px;top:1836px">Learn More</div>

<section class="request abs" role="img" aria-label="Soft blurred photo of a woman in an office"></section>
<h2 class="request-title abs">Request Information</h2>
<div class="field abs" style="left:227px;top:2097px">First Name</div>
<div class="field abs" style="left:481px;top:2097px">Last Name</div>
<div class="field abs" style="left:734px;top:2097px">Company Name</div>
<div class="field abs" style="left:227px;top:2144px">Phone number</div>
<div class="field abs" style="left:481px;top:2144px">Email address</div>
<div class="field abs" style="left:734px;top:2144px">Property Instred In</div>
<div class="submit abs">SUBMIT</div>

<footer class="site-footer abs"></footer>
<nav class="footer-nav abs"><span>HOME</span><span>PROPERTIES</span><span>VIRTUAL TOURS &amp; VIDEOS</span><span>PHOTOS</span><span>BROKER REFERRALS</span></nav>
<p class="copyright abs">© 2016 Company Name &nbsp;All right reserved &nbsp;Term of Use</p>
<div class="social abs"><span></span><span></span><span></span><span></span></div>

</body>
</html>
```